Business Card Design Project

I require a business card with the following information on them for various different people;
name
m:
f:
e:
I have a logo already and will attached that. We are in the construction industry. I require something clean and simple but eye catching at the same time. You can use another colour with our logo if you like and you can style the logo as well if you wish. I am open.
Also it needs to be front and back design.
Industry/Entity Type
Construction
Requirements
Must have
- Logo, name, mobile, fax and email address.
Front and back design

```html
<!DOCTYPE html>
<html lang="en">
<head>
<meta charset="UTF-8">
<title>Stonebridge Builders – Business Cards</title>
<link rel="stylesheet" href="https://fonts.googleapis.com/css2?family=Open+Sans:wght@400;700&display=swap">
<style>
  :root{
    --page-bg:#ece7e1;
    --card-white:#ffffff;
    --brand-green:#55ab3c;
    --brand-green-light:#9fd05a;
    --brand-green-dark:#3f9a34;
    --swoosh-black:#111111;
    --silver-light:#f2f3f4;
    --silver-dark:#c4c6c9;
    --card-edge:#3a3a3a;
    --text-white:#ffffff;
  }
  html,body{margin:0;padding:0;overflow:hidden;}
  body{
    width:1200px;height:757px;position:relative;
    background:var(--page-bg);
    font-family:"Open Sans",Arial,sans-serif;
  }
  .card{
    position:absolute;width:513px;height:293px;
    border-radius:16px;overflow:hidden;
    border:1px solid var(--card-edge);
    box-sizing:border-box;background:var(--card-white);
  }
  .card--front{left:74px;top:54px;}
  .card--back{left:622px;top:54px;}
  .card--alt{left:359px;top:398px;
    background:linear-gradient(110deg,var(--silver-light) 0%,#e1e2e4 55%,var(--silver-dark) 100%);}
  .card__art{position:absolute;inset:0;width:100%;height:100%;}
  .brand{
    position:absolute;display:flex;align-items:center;gap:10px;
    color:var(--brand-green);font-weight:400;white-space:nowrap;line-height:1;
  }
  .brand__square{width:26px;height:26px;background:var(--brand-green);border-radius:3px;flex:none;}
  .card--front .brand{left:44px;top:56px;font-size:30px;}
  .card--back .brand{left:50%;top:50%;transform:translate(-50%,-50%);font-size:38px;}
  .card--back .brand__square{width:32px;height:32px;}
  .card--alt .brand{right:22px;top:200px;font-size:24px;}
  .holder{
    position:absolute;left:42px;top:174px;margin:0;
    font-size:15px;font-weight:700;color:var(--brand-green);
  }
  .contacts{
    position:absolute;right:24px;top:206px;margin:0;padding:0;list-style:none;
    color:var(--text-white);font-size:12px;line-height:21px;text-align:right;
  }
  .contacts li{display:flex;justify-content:flex-end;align-items:center;gap:6px;}
  .contacts svg{width:10px;height:10px;fill:var(--text-white);}
  .emblem-area{
    position:absolute;left:0;top:0;width:218px;height:100%;
    background:linear-gradient(180deg,var(--brand-green-light),var(--brand-green-dark));
  }
</style>
</head>
<body>

<section class="card card--front">
  <svg class="card__art" viewBox="0 0 513 293" preserveAspectRatio="none" aria-hidden="true">
    <defs>
      <linearGradient id="frontGreen" x1="0" y1="1" x2="1" y2="0">
        <stop offset="0" stop-color="#4ea63a"/>
        <stop offset="0.6" stop-color="#9fd05a"/>
        <stop offset="1" stop-color="#4ea63a"/>
      </linearGradient>
    </defs>
    <path d="M0,262 C170,292 400,230 513,18 V293 H0 Z" fill="url(#frontGreen)"/>
    <path d="M0,214 C120,262 270,250 370,160 C265,240 120,268 0,246 Z" fill="var(--swoosh-black)"/>
  </svg>
  <div class="brand"><span class="brand__square"></span>Stonebridge Builders</div>
  <p class="holder">Your Name , Title</p>
  <ul class="contacts">
    <li>+91 98765 43210
      <svg viewBox="0 0 10 10"><rect x="3" y="0" width="4" height="10" rx="1"/></svg></li>
    <li>+91 98765 43210
      <svg viewBox="0 0 10 10"><rect x="0" y="4" width="10" height="6" rx="1"/><rect x="2" y="1" width="6" height="3"/></svg></li>
    <li>hello@stonebridgemail.com
      <svg viewBox="0 0 10 10"><rect x="0" y="2" width="10" height="7"/></svg></li>
  </ul>
</section>

<section class="card card--back">
  <div class="brand"><span class="brand__square"></span>Stonebridge Builders</div>
</section>

<section class="card card--alt">
  <div class="emblem-area" role="img" aria-label="Large green brand emblem decoration"></div>
  <div class="brand">Stonebridge Builders</div>
</section>

</body>
</html>
```